NZ First of it's kind solutions directory and marketplace for busy Mums needs a business card design

We need a business card design for our new nationwide business in NZ (long term plans to go global). We provide solutions to the everyday challenges that busy Mums face by connecting them with quality communities and suppliers of carefully selected, relevant products and services. We sell direct via our online marketplace. The final design should communicate our values of inclusivity, quality and smart solutions. Colours should incorporate our logo colour palette of #477077 and #6ba8b2. Our website is at https://www.brightnestmums.example

Target Market(s)

busy Mums, Age 28 – 50, female, income over $100K, location main centres NZ primarily but NZ wide. Is likely juggling work or career with a young family. Probably had hobbies which have fallen by the wayside.
-Wants to succeed in her chosen career without compromising on family life
-to successfully juggle her career without feeling like she is compromising her children
- Is time poor, something always has to give and it’s generally her health (she’ll stay up late, get stressed)
- probably ex corporate or professional career. Has discretional income

Industry/Entity Type

Business

Contact Information for Business Card

Lena Forbisher, Founder, BrightNestMums.example (Strapline Tap; Gather; Sorted), 47 Kowhai Terrace, Ellerslie, Auckland 1051, New Zealand. Mob: 021 483 517 Ph: +64 (0)9 571 4860

Font styles to use
Other font styles liked:
• Raleway, and/or Architects Daughter

Colors
00a990
33b8a4
86cfc6
cfeae6

Requirements
Must have
• the above details, streamline. the logo and colours associated with those logos
Should not have
• foil or metallic colours

```html
<!DOCTYPE html>
<html lang="en">
<head>
<meta charset="utf-8">
<title>BrightNestMums – Business Card</title>
<link rel="stylesheet" href="https://fonts.googleapis.com/css2?family=Signika:wght@400;600&family=Roboto+Condensed:ital,wght@0,400;1,400&display=swap">
<style>
  :root {
    --teal-deep: #3d5e68;
    --teal-light: #5a9aa3;
    --ink: #3a3f44;
    --card: #f7f7f6;
    --backdrop: #e6e6e6;
    --shadow: rgba(0, 0, 0, 0.28);
  }
  * { margin: 0; padding: 0; box-sizing: border-box; }
  html, body {
    width: 1200px;
    height: 576px;
    overflow: hidden;
    background: var(--backdrop);
  }
  .canvas { position: relative; width: 1200px; height: 576px; }
  .card {
    position: absolute;
    top: 138px;
    width: 484px;
    height: 294px;
    background: var(--card);
    border-radius: 14px;
    overflow: hidden;
    box-shadow: 2px 3px 5px var(--shadow);
  }
  .card--front { left: 82px; }
  .card--back { left: 602px; width: 481px; }

  /* Front */
  .brand-dot {
    position: absolute;
    left: 50%;
    top: 62px;
    width: 56px;
    height: 56px;
    margin-left: -28px;
    border-radius: 50%;
    background: var(--teal-deep);
  }
  .brand-name {
    position: absolute;
    left: 0; right: 0;
    top: 160px;
    text-align: center;
    font-family: "Signika", sans-serif;
    font-weight: 600;
    font-size: 33px;
    letter-spacing: -0.5px;
    color: var(--teal-deep);
  }
  .strapline {
    position: absolute;
    left: 0; right: 0;
    top: 208px;
    text-align: center;
    font-family: "Roboto Condensed", sans-serif;
    font-size: 10.5px;
    letter-spacing: 3.6px;
    color: var(--ink);
  }
  .strapline .divider { color: var(--teal-light); margin: 0 6px; }

  /* Back */
  .side-panel { position: absolute; left: 0; top: 0; width: 250px; height: 294px; }
  .panel-mark {
    position: absolute;
    left: 68px;
    top: 93px;
    width: 100px;
    height: 100px;
    border-radius: 50%;
    background: var(--card);
  }
  .holder {
    position: absolute;
    right: 26px;
    top: 30px;
    text-align: right;
  }
  .holder-name {
    font-family: "Signika", sans-serif;
    font-weight: 600;
    font-size: 20px;
    color: var(--ink);
    line-height: 1.1;
  }
  .holder-role {
    font-family: "Roboto Condensed", sans-serif;
    font-style: italic;
    font-size: 11.5px;
    color: var(--teal-deep);
  }
  .address {
    position: absolute;
    right: 26px;
    top: 156px;
    text-align: right;
    font-family: "Roboto Condensed", sans-serif;
    font-size: 12.5px;
    line-height: 18px;
    color: var(--ink);
  }
  .contact-list {
    position: absolute;
    right: 14px;
    top: 201px;
    list-style: none;
    font-family: "Roboto Condensed", sans-serif;
    font-size: 12.5px;
    line-height: 18.3px;
    color: var(--ink);
  }
  .contact-list li { display: flex; justify-content: flex-end; align-items: center; gap: 7px; }
  .contact-list svg { width: 10px; height: 10px; fill: var(--teal-deep); flex: none; }
</style>
</head>
<body>
<main class="canvas">
  <section class="card card--front" aria-label="Card front">
    <span class="brand-dot" aria-hidden="true"></span>
    <h1 class="brand-name">BrightNestMums</h1>
    <p class="strapline">TAP<span class="divider">|</span>GATHER<span class="divider">|</span>SORTED</p>
  </section>

  <section class="card card--back" aria-label="Card back">
    <svg class="side-panel" viewBox="0 0 250 294" aria-hidden="true">
      <path d="M0 0 H204 Q264 147 226 294 H0 Z" fill="var(--teal-light)"/>
      <path d="M0 0 H195 Q254 147 216 294 H0 Z" fill="var(--teal-deep)"/>
    </svg>
    <span class="panel-mark" aria-hidden="true"></span>

    <div class="holder">
      <p class="holder-name">Lena Forbisher</p>
      <p class="holder-role">Founder</p>
    </div>

    <address class="address">
      47 Kowhai Terrace, Ellerslie,<br>
      Auckland 1051, New Zealand
    </address>

    <ul class="contact-list">
      <li>021 483 517
        <svg viewBox="0 0 10 10"><rect x="2.5" y="0.5" width="5" height="9" rx="1"/><rect x="3.3" y="1.6" width="3.4" height="5.6" fill="var(--card)"/></svg>
      </li>
      <li>+64 (0)9 571 4860
        <svg viewBox="0 0 10 10"><path d="M1 3.5 Q5 0.5 9 3.5 L8 5 L6.5 4 V3 H3.5 V4 L2 5 Z"/><rect x="2" y="5.5" width="6" height="3.5" rx="0.6"/></svg>
      </li>
      <li>www.BrightNestMums.example
        <svg viewBox="0 0 10 10"><rect x="0.5" y="2" width="9" height="6.5"/><path d="M0.8 2.3 L5 5.8 L9.2 2.3" stroke="var(--card)" stroke-width="0.8" fill="none"/></svg>
      </li>
      <li>lena@brightnestmums.example
        <svg viewBox="0 0 10 10"><circle cx="5" cy="5" r="4.5"/><path d="M0.5 5 H9.5 M5 0.5 V9.5 M5 0.5 Q2 5 5 9.5 M5 0.5 Q8 5 5 9.5" stroke="var(--card)" stroke-width="0.6" fill="none"/></svg>
      </li>
    </ul>
  </section>
</main>
</body>
</html>
```